Business Card - Tidal Lanes

Need Business Card design for company named Tidal Lanes. Software development focused mainly on Brindle Orvix & Zelt Apps. I've attached our logo with both a black and white background. Please add trademark symbol to logo when using.

```html
<!DOCTYPE html>
<html lang="en">
<head>
<meta charset="utf-8">
<title>Tidal Lanes — Business Card</title>
<link rel="stylesheet" href="https://fonts.googleapis.com/css2?family=Open+Sans:wght@400;600;700&display=swap">
<style>
  :root {
    --page: #ecebe8;
    --card-black: #050505;
    --band-yellow: #f7b517;
    --band-orange: #f29a2e;
    --rule-red: #c8161d;
    --ink-dark: #1a1a1a;
    --ink-light: #ffffff;
    --ink-muted: #d9d9d9;
    --mark-faint: rgba(200, 120, 40, 0.22);
  }
  * { box-sizing: border-box; margin: 0; padding: 0; }
  html, body {
    width: 1200px; height: 720px; overflow: hidden;
    background: var(--page);
    font-family: "Open Sans", Arial, sans-serif;
  }
  .canvas {
    position: relative; width: 1200px; height: 720px;
    display: flex; align-items: center; justify-content: center; gap: 40px;
  }
  .card {
    position: relative; width: 540px; height: 309px;
    background: var(--card-black); overflow: hidden;
    box-shadow: 0 6px 18px rgba(0,0,0,0.18);
  }

  /* Front */
  .band {
    position: absolute; left: 0; right: 0; height: 44px;
    background: linear-gradient(90deg, var(--band-yellow), var(--band-orange));
    display: flex; align-items: center; justify-content: center;
    color: var(--ink-dark);
  }
  .band--top { top: 0; border-bottom: 3px solid var(--rule-red); }
  .band--bottom { bottom: 0; border-top: 3px solid var(--rule-red); }
  .band::after {
    content: ""; position: absolute; left: 0; right: 0; height: 10px; background: var(--card-black);
  }
  .band--top::after { bottom: -13px; }
  .band--bottom::after { top: -13px; }
  .holder-name { font-weight: 700; font-size: 17px; }
  .holder-title { font-weight: 400; font-size: 13px; }
  .address { font-size: 12.5px; font-weight: 600; letter-spacing: 0.2px; }

  .brand {
    position: absolute; left: 0; right: 0; top: 82px;
    display: flex; flex-direction: column; align-items: center; gap: 10px;
  }
  .brand-dot {
    width: 34px; height: 34px; border-radius: 50%;
    background: var(--band-orange);
  }
  .wordmark {
    color: var(--ink-light); font-weight: 700; font-size: 26px; letter-spacing: -0.5px;
  }
  .wordmark sup { font-size: 9px; font-weight: 700; margin-left: 2px; vertical-align: 14px; }

  .contacts {
    position: absolute; left: 0; right: 0; top: 200px;
    display: flex; justify-content: center; gap: 26px;
    color: var(--ink-light); font-size: 14px;
  }
  .contact { display: flex; align-items: center; gap: 6px; }
  .contact svg { width: 12px; height: 14px; fill: var(--ink-light); }

  /* Back */
  .back-mark {
    position: absolute; left: 180px; top: 30px; width: 200px; height: 200px;
    border-radius: 50%; background: var(--mark-faint);
  }
  .back-wordmark {
    position: absolute; left: 0; right: 0; top: 112px; text-align: center;
    color: var(--ink-light); font-weight: 700; font-size: 54px; letter-spacing: -1.5px;
  }
  .back-wordmark sup { font-size: 14px; vertical-align: 30px; margin-left: 3px; }
  .web {
    position: absolute; right: 118px; bottom: 60px;
    color: var(--ink-muted); font-size: 14px; letter-spacing: 0.6px;
  }
</style>
</head>
<body>
<main class="canvas">
  <section class="card card--front" aria-label="Card front">
    <div class="band band--top">
      <p><span class="holder-name">Your Name,</span> <span class="holder-title">Title</span></p>
    </div>
    <div class="brand">
      <span class="brand-dot"></span>
      <p class="wordmark">Tidal Lanes<sup>TM</sup></p>
    </div>
    <div class="contacts">
      <p class="contact">
        <svg viewBox="0 0 12 16" aria-hidden="true"><path d="M2 0h8a2 2 0 0 1 2 2v12a2 2 0 0 1-2 2H2a2 2 0 0 1-2-2V2a2 2 0 0 1 2-2zm0 2v9h8V2zm4 10.5a1 1 0 1 0 0 2 1 1 0 0 0 0-2z"/></svg>
        555-204-7710
      </p>
      <p class="contact">
        <svg viewBox="0 0 16 14" aria-hidden="true" style="width:15px"><path d="M3 1h10l3 5v6a1 1 0 0 1-1 1h-2v-2H3v2H1a1 1 0 0 1-1-1V6zm1.2 1.6L2.3 6h11.4l-1.9-3.4zM3 8a1 1 0 1 0 0 2 1 1 0 0 0 0-2zm10 0a1 1 0 1 0 0 2 1 1 0 0 0 0-2z"/></svg>
        555-204-7735
      </p>
    </div>
    <div class="band band--bottom">
      <p class="address">4120 Harbor Row, Tern Bay, FL 34009</p>
    </div>
  </section>

  <section class="card card--back" aria-label="Card back">
    <span class="back-mark"></span>
    <p class="back-wordmark">Tidal Lanes<sup>TM</sup></p>
    <p class="web">www.tidallanes.com</p>
  </section>
</main>
</body>
</html>
```